We want to revamp our current website -www.kelvota-eng.com

We need to have a new website for our company that offers non-destructive and testing solutions around Africa. We have a current website but it does not fulfil our needs as it is:<br/>1. Not clear and bright<br/>2. Does not fit well in mobile <br/>3. Is not easily updatable by our staff. <br/>4. Is not linked to our social media sites.<br/>We would like to have a website that addresses the above issues. Our colours are Red and Blue and should communicate to our clients, that we are a professional company open for business, ready to solve their non-destructive testing problems around Africa. * Helpful if it is a wordpress website.

Target Market(s)

Our customers are B2B Corporate clients. We mainly work in
1. Storage Terminals
2. Refineries
3. Oil and Gas offshore and onshore rigs.

Industry/Entity Type

Oil And Gas

Contact Information for Business Card

Please find our current business card on the uploaded files.

Coding

Coded - Design and coding required

Number of Pages Required

5+ page

Font styles to use
Serif
Sans Serif

Requirements
Must have
• I like this site www.pirelo-inspection.com They are in the same industry.
• I don't understand how to call them but all the 'call to action' buttons, and links to our Social media pages.
• Must have a place where we update information in a regular basis. A Blog!

```html
<!DOCTYPE html>
<html lang="en">
<head>
<meta charset="utf-8">
<title>Kelvota Engineering</title>
<link href="https://fonts.googleapis.com/css2?family=Poppins:wght@300;400;600;700&family=Roboto:wght@400;500;700&display=swap" rel="stylesheet">
<style>
:root{
  --red:#a3111a;
  --red-dark:#8c0c14;
  --navy:#1f2b6c;
  --navy-dark:#18224f;
  --ink:#1c1c1c;
  --text:#555;
  --muted:#777;
  --line:#e3e3e3;
  --soft:#f4f4f6;
  --lav:#c9cdf2;
}
*{margin:0;padding:0;box-sizing:border-box}
html,body{width:1200px;height:4335px;overflow:hidden}
body{font-family:"Roboto",Arial,sans-serif;color:var(--text);background:#fff;position:relative}
section,header,footer{position:relative;width:1200px;overflow:hidden}
.abs{position:absolute}
.h-title{font-family:"Poppins",sans-serif;font-size:34px;color:var(--ink);text-align:center;font-weight:300}
.h-title b{font-weight:700}

/* header */
.site-header{height:110px;background:#fff}
.brand{left:111px;top:26px;display:flex;align-items:center;gap:12px}
.brand-dot{width:58px;height:58px;border-radius:50%;background:var(--navy)}
.brand-name{font-family:"Poppins",sans-serif;font-weight:600;font-size:20px;line-height:24px;color:var(--red)}
.nav{left:392px;top:54px;display:flex;gap:27px;font-size:14px;font-weight:500;color:#222}
.nav .active{color:var(--red)}
.nav .caret{font-size:10px}
.phone-btn{left:935px;top:45px;width:153px;height:40px;border-radius:20px;background:var(--red);color:#fff;font-size:15px;font-weight:700;display:flex;align-items:center;justify-content:center;gap:8px}

/* hero */
.hero{height:530px;background:linear-gradient(180deg,#4a4d8e 0%,#8d5f95 30%,#b97a6a 55%,#5e4136 80%,#2d2622 100%)}
.hero-box{left:300px;top:125px;width:600px;height:200px;background:rgba(40,40,60,.45)}
.hero h1{left:0;width:1200px;top:145px;text-align:center;font-family:"Poppins",sans-serif;font-size:44px;color:#fff;font-weight:300}
.hero h1 b{font-weight:700}
.hero p{left:300px;width:600px;top:222px;text-align:center;color:#fff;font-size:18px;line-height:30px}
.hero-btn{left:490px;top:315px;width:222px;height:57px;border-radius:29px;background:var(--red);color:#fff;font-family:"Poppins",sans-serif;font-weight:700;font-size:18px;display:flex;align-items:center;justify-content:center}
.hero-arrow{top:357px;width:40px;height:40px;border:2px solid #fff;border-radius:50%}

/* industries */
.industries{height:135px;background:#fff}
.industry{top:0;width:195px;height:135px;text-align:center;font-size:15px;color:#444;border-right:1px solid var(--line)}
.industry svg{margin-top:22px}
.industry span{display:block;margin-top:6px;line-height:19px}
.industry.active{background:#fff;color:var(--navy)}
.industry.active span{margin-top:5px;line-height:18px}
.industry .thumb{height:92px;background:linear-gradient(180deg,#3c4a8e,#c47a4c 60%,#2f2a2a)}

/* about */
.about{height:644px;background:var(--soft)}
.about .h-title{position:absolute;top:72px;width:1200px}
.sub{position:absolute;width:1200px;text-align:center;font-size:15px;color:#444}
.tl-line{left:177px;top:190px;width:1px;height:340px;background:#ccc}
.tl-item{left:111px;font-size:11px;line-height:15px;color:#444;width:58px}
.tl-dot{left:172px;width:11px;height:11px;border-radius:50%;background:#aaa}
.tl-dot.on{background:var(--navy)}
.snap-title{left:226px;top:187px;font-family:"Poppins",sans-serif;font-size:17px;color:var(--navy)}
.snap-list{left:226px;top:234px;list-style:none;font-size:14px;color:#444}
.snap-list li{height:32.5px;display:flex;align-items:center;gap:14px}
.tick{width:11px;height:11px;border-radius:50%;background:var(--red);flex:none}
.video{left:640px;top:181px;width:448px;height:364px;background:linear-gradient(160deg,#9fb2c4,#c2b6a3 45%,#6a6b4a 75%,#4a4a3a)}
.play{left:192px;top:150px;width:66px;height:66px;border-radius:50%;background:var(--red);border:4px solid rgba(255,255,255,.6)}

/* services */
.services{height:458px;background:#fff}
.svc-title{top:76px;font-family:"Poppins",sans-serif;font-weight:700;font-size:30px;color:#fff}
.svc-text{top:128px;width:315px;color:#fff;font-size:15px;line-height:27.5px;text-align:justify}
.svc-btn{top:331px;width:176px;height:48px;border-radius:24px;background:#fff;font-family:"Poppins",sans-serif;font-weight:600;font-size:14px;display:flex;align-items:center;justify-content:center;gap:10px}

/* values */
.values{height:657px;background:#fff}
.values .h-title{position:absolute;top:58px;width:1200px}
.values-intro{left:200px;width:800px;top:120px;text-align:center;font-size:15px;line-height:26px;color:#444}
.card{top:198px;width:305px;height:340px;text-align:center}
.card.raised{background:#fff;box-shadow:0 3px 14px rgba(0,0,0,.15)}
.card .ring{margin:26px auto 0;width:124px;height:124px;border-radius:50%;background:var(--lav);display:flex;align-items:center;justify-content:center}
.card .core{width:106px;height:106px;border-radius:50%;background:var(--navy-dark);display:flex;align-items:center;justify-content:center}
.card h3{margin-top:22px;font-size:18px;font-weight:500;color:#111}
.card p{margin:20px auto 0;width:250px;font-size:14px;line-height:24px;color:#555}
.card .more{margin-top:24px;font-size:14px;font-weight:700;color:var(--red)}

/* why */
.why{height:392px;background:var(--red)}
.why-photo{left:0;top:0}
.why h2{left:651px;top:64px;font-family:"Poppins",sans-serif;font-size:35px;color:#fff;font-weight:300}
.why h2 b{font-weight:700}
.why ul{left:651px;top:136px;list-style:none;color:#fff;font-size:15px}
.why li{height:32.6px;display:flex;align-items:center;gap:14px}
.why .tick{background:#fff}

/* blog */
.blog{height:758px;background:#fff}
.blog .h-title{position:absolute;top:100px;width:1200px}
.post{top:184px;width:309px;height:465px;border:1px solid #e6e6e6;box-shadow:0 2px 8px rgba(0,0,0,.06);text-align:center}
.post .img{height:232px}
.post h3{margin-top:30px;font-size:20px;font-weight:500;color:#222}
.post p{margin:22px auto 0;width:275px;font-size:13px;line-height:28px;color:#666}
.post .rule{margin:24px auto 0;width:265px;height:1px;background:#ddd}
.post .meta{margin-top:20px;font-size:13px;color:#666}

/* clients */
.clients{height:286px;background:var(--soft)}
.clients .h-title{position:absolute;top:46px;width:1200px}
.client{top:114px;width:181px;height:86px;background:#fff;display:flex;align-items:center;justify-content:center;gap:8px;font-family:"Roboto",sans-serif;font-weight:700;font-size:16px;color:var(--red)}
.client i{width:12px;height:12px;background:var(--red);display:block}

/* footer */
.site-footer{height:363px;background:var(--navy)}
.f-col{top:84px;color:#fff}
.f-col h4{font-size:17px;font-weight:500;letter-spacing:.3px;margin-bottom:20px}
.f-col ul{list-style:none;font-size:15px}
.f-col li{height:33px}
.f-col li::before{content:"»";margin-right:10px}
.contact li::before{content:none}
.contact li{display:flex;gap:14px;height:auto;margin-bottom:12px;line-height:24px}
.contact svg{flex:none;margin-top:5px}
.news{left:820px;top:84px;color:#fff}
.news h4{font-size:17px;font-weight:500;margin-bottom:20px}
.sub-form{width:268px;height:40px;border-radius:20px;background:#fff;display:flex;align-items:center;justify-content:space-between;padding-left:18px;font-size:14px;color:#888}
.sub-form span{height:40px;width:95px;border-radius:20px;background:var(--red);color:#fff;font-weight:700;display:flex;align-items:center;justify-content:center}
.socials{display:flex;gap:8px;margin-top:14px}
.socials div{width:36px;height:36px;border-radius:50%;background:#fff;display:flex;align-items:center;justify-content:center}
.copy{left:0;width:1200px;top:322px;text-align:center;color:#fff;font-size:15px}
</style>
</head>
<body>

<header class="site-header">
  <div class="abs brand"><div class="brand-dot"></div><div class="brand-name">Kelvota<br>Engineering</div></div>
  <nav class="abs nav"><span class="active">Home</span><span>About Us</span><span>Services <span class="caret">▼</span></span><span>Blog</span><span>Contact Us</span>
    <svg width="16" height="16" viewBox="0 0 16 16"><circle cx="6.5" cy="6.5" r="5" fill="none" stroke="#222" stroke-width="2"/><path d="M10 10l5 5" stroke="#222" stroke-width="2"/></svg>
    <span>Eng <span class="caret">⌄</span></span></nav>
  <div class="abs phone-btn"><svg width="14" height="14" viewBox="0 0 24 24"><path fill="#fff" d="M6.6 10.8a15 15 0 006.6 6.6l2.2-2.2a1 1 0 011-.25 11.4 11.4 0 003.6.6 1 1 0 011 1V20a1 1 0 01-1 1A17 17 0 013 4a1 1 0 011-1h3.5a1 1 0 011 1c0 1.25.2 2.45.6 3.6a1 1 0 01-.25 1z"/></svg>800 555 0142</div>
</header>

<section class="hero" role="img" aria-label="Refinery storage tanks and towers lit at dusk">
  <div class="abs hero-box"></div>
  <h1 class="abs"><b>Kelvota</b> Refineries</h1>
  <p class="abs">With roots in Mombasa, we have over 15 years' experience in NDT, Mechanical engineering and Marine services.</p>
  <div class="abs hero-btn">GET STARTED</div>
  <div class="abs hero-arrow" style="left:33px"><svg width="36" height="36" viewBox="0 0 36 36"><path d="M21 11l-7 7 7 7" fill="none" stroke="#fff" stroke-width="2"/></svg></div>
  <div class="abs hero-arrow" style="left:1128px"><svg width="36" height="36" viewBox="0 0 36 36"><path d="M15 11l7 7-7 7" fill="none" stroke="#fff" stroke-width="2"/></svg></div>
</section>

<section class="industries">
  <div class="abs industry" style="left:111px"><svg width="60" height="56" viewBox="0 0 60 56" fill="none" stroke="#555" stroke-width="2"><rect x="6" y="10" width="22" height="40"/><rect x="30" y="22" width="24" height="28"/><path d="M6 18h22M30 30h24"/></svg><span>Oil Storage &amp; Transport</span></div>
  <div class="abs industry active" style="left:307px"><div class="thumb" role="img" aria-label="Refinery plant at dusk"></div><span>Refineries &amp;<br>Petrochemicals</span></div>
  <div class="abs industry" style="left:503px"><svg width="60" height="56" viewBox="0 0 60 56" fill="none" stroke="#555" stroke-width="2"><path d="M14 50L22 8h8l8 42M18 30h16M40 20h12v30H40z"/></svg><span>Oil and Gas</span></div>
  <div class="abs industry" style="left:698px"><svg width="60" height="56" viewBox="0 0 60 56" fill="none" stroke="#555" stroke-width="2"><path d="M10 50V14h30M10 14l10 36M40 14v10M30 50h22M44 30a6 6 0 100 .1"/></svg><span>Mining</span></div>
  <div class="abs industry" style="left:893px;border-right:none"><svg width="60" height="56" viewBox="0 0 60 56" fill="none" stroke="#555" stroke-width="2"><path d="M30 4L18 52M30 4l12 48M16 16h28M14 28h32M22 40h16"/></svg><span>Power Generation</span></div>
</section>

<section class="about">
  <h2 class="h-title"><b>About</b> Kelvota</h2>
  <p class="sub" style="top:128px">Welcome To non-destructive and testing solutions</p>
  <div class="abs tl-line"></div>
  <div class="abs tl-item" style="top:190px">Founded<br>in 2007</div><div class="abs tl-dot" style="top:192px"></div>
  <div class="abs tl-item" style="top:298px">A<br>Snapshot</div><div class="abs tl-dot on" style="top:295px"></div>
  <div class="abs tl-item" style="top:387px">Works in<br>20+<br>Countries<br>in Africa</div><div class="abs tl-dot" style="top:387px"></div>
  <div class="abs tl-item" style="top:512px">Who We<br>Are</div><div class="abs tl-dot" style="top:512px"></div>
  <div class="abs snap-title">A Snapshot</div>
  <ul class="abs snap-list">
    <li><i class="tick"></i>Certified API Inspectors on Hire</li>
    <li><i class="tick"></i>Certified ASNT SNT-TC-1A Level II Technicians</li>
    <li><i class="tick"></i>Professional Engineers on hire.</li>
    <li><i class="tick"></i>More than 200 Inspections carried out to date.</li>
    <li><i class="tick"></i>1 NDT Laboratory.</li>
    <li><i class="tick"></i>NDT and ADVANCED NDT Solutions Provider.</li>
    <li><i class="tick"></i>100% Commitment to Safety.</li>
    <li><i class="tick"></i>10+ Partners worldwide.</li>
    <li><i class="tick"></i>Mechanical Services Division</li>
  </ul>
  <div class="abs video" role="img" aria-label="Storage tank with yellow pipework on site">
    <div class="abs play"><svg width="58" height="58" viewBox="0 0 58 58"><path d="M23 17l17 12-17 12z" fill="#fff"/></svg></div>
  </div>
</section>

<section class="services">
  <svg class="abs" style="left:0;top:0" width="1200" height="458" viewBox="0 0 1200 458" role="img" aria-label="Inspection and engineering work photos tinted red and blue">
    <polygon points="0,0 600,68 600,395 0,458" fill="#a3111a"/>
    <polygon points="600,68 1200,0 1200,458 600,395" fill="#25306f"/>
    <path d="M598 60 C 430 150, 700 190, 560 240 C 440 285, 560 360, 740 395 L 600 400 C 470 370, 410 290, 520 240 C 610 200, 390 140, 598 60 Z" fill="#fff"/>
  </svg>
  <h2 class="abs svc-title" style="left:111px">Inspection Services</h2>
  <p class="abs svc-text" style="left:111px">Our Inspection team has the technical capability, backed by the right equipment to provide full range solutions in accordance with the client's requirement, and in compliance with local and international standards. We offer the following inspection services</p>
  <div class="abs svc-btn" style="left:111px;color:var(--red)">LEARN MORE</div>
  <h2 class="abs svc-title" style="left:775px">Engineering Services</h2>
  <p class="abs svc-text" style="left:775px">Our Mechanical Engineering division is majorly involved with ASME compliant steel fabrication and welding both at our workshop and on client sites. With our corporate culture of quality, we have engaged a team of well-specialized technicians</p>
  <div class="abs svc-btn" style="left:775px;color:var(--navy)">LEARN MORE</div>
</section>

<section class="values">
  <h2 class="h-title"><b>Our</b> Values</h2>
  <p class="abs values-intro">Respect and diversity, ethics and integrity, safety and sustainability are important elements of our values. They are our foundation. But what clearly sets Kelvota apart from other companies are three core values.</p>
  <div class="abs card" style="left:111px"><div class="ring"><div class="core">
    <svg width="56" height="56" viewBox="0 0 56 56" fill="none" stroke="#fff" stroke-width="2"><circle cx="28" cy="28" r="9"/><circle cx="28" cy="28" r="17" stroke-dasharray="6 5"/><path d="M28 4v6M28 46v6M4 28h6M46 28h6"/></svg>
  </div></div><h3>Passion for innovation</h3><p>Our customer is at the center of all innovation. We encourage innovation not only in products and services</p><div class="more">READ MORE ➔</div></div>
  <div class="abs card raised" style="left:447px"><div class="ring"><div class="core">
    <svg width="56" height="56" viewBox="0 0 56 56" fill="none" stroke="#fff" stroke-width="2"><circle cx="22" cy="22" r="8"/><path d="M8 48c0-9 6-15 14-15s14 6 14 15"/><rect x="32" y="6" width="18" height="12" rx="2"/><path d="M36 18l-2 5 6-5"/></svg>
  </div></div><h3>Customer Obsession</h3><p>The wants, wishes, and views of our customers guide our every action. We are curious about our customers</p><div class="more">READ MORE ➔</div></div>
  <div class="abs card" style="left:783px"><div class="ring"><div class="core">
    <svg width="56" height="56" viewBox="0 0 56 56" fill="none" stroke="#fff" stroke-width="2"><rect x="10" y="8" width="36" height="40" rx="2"/><path d="M16 38l8-9 7 5 10-12M36 22h5v5"/></svg>
  </div></div><h3>Drive for results</h3><p>We strive for a visible, measurable and balanced benefit from everything we do. We focus on the essential</p><div class="more">READ MORE ➔</div></div>
</section>

<section class="why">
  <svg class="abs why-photo" width="600" height="392" viewBox="0 0 600 392" role="img" aria-label="Inspector in hard hat checking a pipeline near storage tanks">
    <defs><linearGradient id="whyg" x1="0" y1="0" x2="1" y2="1"><stop offset="0" stop-color="#7f96ad"/><stop offset=".5" stop-color="#3e4f6e"/><stop offset="1" stop-color="#8a4a3e"/></linearGradient></defs>
    <polygon points="0,0 528,0 598,392 0,392" fill="url(#whyg)"/>
  </svg>
  <h2 class="abs"><b>Why Use</b> Kelvota?</h2>
  <ul class="abs">
    <li><i class="tick"></i>Kenyan Based Company With International Expertise</li>
    <li><i class="tick"></i>Fast, Effective Mobilization</li>
    <li><i class="tick"></i>International Standards</li>
    <li><i class="tick"></i>12 Years Of Experience</li>
    <li><i class="tick"></i>Solutions Focused</li>
    <li><i class="tick"></i>Technical Excellence Ensures Any Job Can Be Tackled</li>
  </ul>
</section>

<section class="blog">
  <h2 class="h-title"><b>Latest</b> Blog</h2>
  <article class="abs post" style="left:111px"><div class="img" role="img" aria-label="Technician testing a pipe weld" style="background:linear-gradient(135deg,#6d6a63,#c8c2b8 50%,#5560b8)"></div><h3>Sed ut perspiciatis unde</h3><p>Nemo enim ipsam voluptatem quia voluptas sit aspernatur aut odit aut fugit, sed quia con ratione voluptatem sequi nesciunt.</p><div class="rule"></div><div class="meta">Comment (02) &nbsp;&nbsp; | &nbsp;&nbsp; 05 February 2020</div></article>
  <article class="abs post" style="left:445px"><div class="img" role="img" aria-label="Welder at work with sparks" style="background:linear-gradient(135deg,#2c1a1a,#a01c1c 55%,#f0b36a)"></div><h3>Sed ut perspiciatis unde</h3><p>Nemo enim ipsam voluptatem quia voluptas sit aspernatur aut odit aut fugit, sed quia con ratione voluptatem sequi nesciunt.</p><div class="rule"></div><div class="meta">Comment (02) &nbsp;&nbsp; | &nbsp;&nbsp; 05 February 2020</div></article>
  <article class="abs post" style="left:779px"><div class="img" role="img" aria-label="Workers in overalls on a pipe structure" style="background:linear-gradient(160deg,#4d8ed0,#8fb8de 45%,#b56a3a)"></div><h3>Sed ut perspiciatis unde</h3><p>Nemo enim ipsam voluptatem quia voluptas sit aspernatur aut odit aut fugit, sed quia con ratione voluptatem sequi nesciunt.</p><div class="rule"></div><div class="meta">Comment (02) &nbsp;&nbsp; | &nbsp;&nbsp; 05 February 2020</div></article>
</section>

<section class="clients">
  <h2 class="h-title"><b>Our</b> Clients</h2>
  <div class="abs client" style="left:111px"><i></i>Norvane Oil</div>
  <div class="abs client" style="left:311px"><i></i>Halden Ridge</div>
  <div class="abs client" style="left:510px"><i></i>Sandrel Energy</div>
  <div class="abs client" style="left:709px"><i></i>Tavira Logistics</div>
  <div class="abs client" style="left:908px"><i></i>Quenor Fuels</div>
</section>

<footer class="site-footer">
  <div class="abs f-col" style="left:111px"><h4>QUICK LINKS</h4><ul><li>Home</li><li>About</li><li>Services</li><li>Blog</li><li>Contact Us</li></ul></div>
  <div class="abs f-col" style="left:311px"><h4>IMPORTANT</h4><ul><li>Terms of Use</li><li>Site Map</li><li>Privacy Policy</li><li>Disclaimer</li></ul></div>
  <div class="abs f-col contact" style="left:523px;width:240px"><h4>CONTACT US</h4><ul>
    <li><svg width="12" height="15" viewBox="0 0 12 15"><path d="M6 0a6 6 0 016 6c0 4-6 9-6 9S0 10 0 6a6 6 0 016-6z" fill="#fff"/><circle cx="6" cy="6" r="2" fill="#1f2b6c"/></svg>Harbour Lane, Plot 41,<br>80100 Port Rella</li>
    <li><svg width="12" height="15" viewBox="0 0 12 15"><rect x="2" y="0" width="8" height="15" rx="2" fill="#fff"/></svg>+ 100 20 555 0610/1</li>
    <li><svg width="14" height="14" viewBox="0 0 14 14"><rect x="1" y="3" width="12" height="10" fill="#fff"/><rect x="3" y="0" width="8" height="4" fill="#fff"/></svg>+100705550182</li>
    <li><svg width="14" height="12" viewBox="0 0 14 12"><rect x="1" y="1" width="12" height="10" fill="none" stroke="#fff" stroke-width="1.5"/><path d="M1 1l6 5 6-5" fill="none" stroke="#fff" stroke-width="1.5"/></svg>info@kelvota-eng.com</li>
  </ul></div>
  <div class="abs news"><h4>NEWSLETTER SUBSCRIPTION</h4><div class="sub-form">Enter your email<span>SUBMIT</span></div>
    <div class="socials">
      <div aria-label="Share"><svg width="16" height="16" viewBox="0 0 16 16" fill="#1f2b6c"><circle cx="12" cy="3" r="2.5"/><circle cx="4" cy="8" r="2.5"/><circle cx="12" cy="13" r="2.5"/><path d="M12 3L4 8l8 5" stroke="#1f2b6c" stroke-width="1.5" fill="none"/></svg></div>
      <div aria-label="Chat"><svg width="16" height="16" viewBox="0 0 16 16"><path d="M2 3h12v8H7l-3 3v-3H2z" fill="#1f2b6c"/></svg></div>
      <div aria-label="Website"><svg width="16" height="16" viewBox="0 0 16 16" fill="none" stroke="#1f2b6c" stroke-width="1.5"><circle cx="8" cy="8" r="6.5"/><path d="M1.5 8h13M8 1.5c3 3 3 10 0 13M8 1.5c-3 3-3 10 0 13"/></svg></div>
      <div aria-label="Email"><svg width="16" height="14" viewBox="0 0 16 14" fill="none" stroke="#1f2b6c" stroke-width="1.5"><rect x="1" y="2" width="14" height="10"/><path d="M1 2l7 6 7-6"/></svg></div>
    </div></div>
  <p class="abs copy">© 2020 Kelvota Engineering &nbsp;| All Rights Reserved | Terms and Conditions</p>
</footer>

</body>
</html>
```